List Now, Launch Later - DL Flyer front & back

Looking for a flyer that has nothing much other than “List Now, Launch Later” on the front with text to fill the back. With image on front that symbolises launch, maybe house being launch like a rocket.
The text has yet to be written but here is the gist: This is for the back of flyer.
List property and delay the launch. In the meantime, we can:
· Prepare contract
· Prepare marketing
· Prepare the property
· Do the Pest and Building Report
· Give the tenants their due notice of sale
· Advise buyers in an off market capacity
This ensures we are first to market when the time comes rather than coming onto the market along with a surge of spring sellers. Buyers are still buying now. The lack of stock is inadvertently creating strength in the market.
The feel has to be modern, clean, contemporary & graphic

```html
<!DOCTYPE html>
<html lang="en">
<head>
<meta charset="utf-8">
<title>List Now, Launch Later – DL Flyer Front &amp; Back</title>
<link rel="stylesheet" href="https://fonts.googleapis.com/css2?family=Montserrat:wght@400;500;600;700;800&display=swap">
<style>
  :root {
    --blue: #2f6fc6;
    --blue-deep: #2a58b0;
    --navy: #2c2d86;
    --violet: #3b3596;
    --orange: #f6a623;
    --paper: #ffffff;
    --mist: #eef0f3;
    --line: #c9ced6;
    --ink: #2b2e3a;
    --muted: #6c7280;
  }
  * { box-sizing: border-box; margin: 0; padding: 0; }
  html, body { width: 784px; height: 1200px; overflow: hidden; background: var(--paper); }
  body { position: relative; font-family: "Montserrat", sans-serif; color: var(--ink); }

  .flyer { position: absolute; width: 306px; height: 496px; overflow: hidden; box-shadow: 0 1px 4px rgba(0,0,0,.12); }
  .flyer--a { left: 52px; top: 47px; }
  .flyer--b { left: 425px; top: 47px; }
  .flyer--c { left: 52px; top: 595px; }
  .flyer--d { left: 425px; top: 595px; }

  /* Front */
  .front__photo { position: absolute; inset: 0; }
  .front--blue .front__photo { background: linear-gradient(160deg, #3f86d6 0%, #2f6fc6 45%, #2459ad 100%); }
  .front--light .front__photo { background: linear-gradient(165deg, #f4f5f7 0%, #e6e9ee 55%, #d5dae2 100%); }
  .launch-mark { position: absolute; left: 28px; top: 44px; width: 92px; height: 92px; border-radius: 18px; }
  .front--blue .launch-mark { background: linear-gradient(135deg, rgba(255,255,255,.55), rgba(255,255,255,.2)); }
  .front--light .launch-mark { background: linear-gradient(135deg, rgba(59,53,150,.45), rgba(246,166,35,.35)); }
  .front__headline { position: absolute; left: 26px; top: 324px; font-size: 31px; line-height: 1.02; font-weight: 800; letter-spacing: -.3px; }
  .front--blue .front__headline { color: var(--paper); }
  .front--light .front__headline { color: var(--violet); }
  .front__arrow { position: absolute; right: 18px; top: 420px; }

  /* Back */
  .back--light { background: var(--mist); }
  .back--dark { background: var(--navy); color: var(--paper); }
  .back__mark { position: absolute; right: 4px; top: -20px; width: 104px; height: 98px; border-radius: 18px; }
  .back--light .back__mark { background: linear-gradient(135deg, rgba(47,111,198,.5), rgba(246,166,35,.4)); }
  .back--dark .back__mark { background: linear-gradient(135deg, rgba(255,255,255,.6), rgba(246,166,35,.45)); }
  .back__title { position: absolute; right: 22px; top: 96px; text-align: left; width: 170px; }
  .back__title strong { display: block; font-size: 21px; font-weight: 800; line-height: 1.05; }
  .back__title span { display: block; font-size: 15px; font-weight: 500; line-height: 1.2; }
  .back--light .back__title strong { color: var(--blue); }
  .back--light .back__title span { color: var(--blue); }
  .back--dark .back__title strong { color: var(--paper); }
  .back--dark .back__title span { color: var(--paper); }

  .tasks { position: absolute; left: 18px; top: 176px; width: 164px; }
  .tasks h3 { font-size: 9px; font-weight: 700; margin-bottom: 6px; }
  .tasks li { list-style: none; display: flex; justify-content: space-between; align-items: center;
              font-size: 5.6px; height: 12px; padding: 0 3px; margin-bottom: 2px; border-bottom: 1px solid var(--line); }
  .back--dark .tasks li { border-bottom-color: rgba(255,255,255,.35); }
  .tasks li i { width: 6px; height: 6px; border: 1px solid var(--orange); border-radius: 1px; }

  .rush { position: absolute; right: 18px; top: 172px; width: 96px; text-align: right; }
  .rush h3 { font-size: 8px; font-weight: 700; margin-bottom: 4px; }
  .rush p { font-size: 5px; line-height: 1.45; color: var(--muted); }
  .back--dark .rush p { color: rgba(255,255,255,.8); }
  .back--light .rush h3 { color: var(--ink); }

  .agent { position: absolute; left: 18px; top: 300px; }
  .agent h4 { font-size: 11px; font-weight: 700; margin-bottom: 6px; }
  .agent p { display: flex; align-items: center; gap: 4px; font-size: 5.5px; margin-bottom: 3px; }
  .agent p i { width: 5px; height: 5px; border-radius: 50%; background: var(--orange); }

  .perks { position: absolute; left: 150px; right: 14px; top: 418px; display: flex; justify-content: space-between; }
  .perks div { width: 30px; text-align: center; font-size: 4.5px; }
  .perks svg { display: block; margin: 0 auto 3px; }
  .back--light .perks { opacity: .35; }
  .back--dark .perks { opacity: .8; }
</style>
</head>
<body>

  <!-- Front, blue -->
  <section class="flyer flyer--a front front--blue">
    <div class="front__photo" role="img" aria-label="Bright living room interior photo under a blue overlay"></div>
    <div class="launch-mark" role="img" aria-label="Launch symbol: house taking off like a rocket"></div>
    <h1 class="front__headline">LIST NOW,<br>LAUNCH<br>LATER.</h1>
    <svg class="front__arrow" width="10" height="14" viewBox="0 0 10 14"><path d="M0 0 L10 7 L0 14 Z" fill="#f6a623"/></svg>
  </section>

  <!-- Back, light -->
  <section class="flyer flyer--b back back--light">
    <div class="back__mark" role="img" aria-label="Launch symbol: house taking off like a rocket"></div>
    <div class="back__title"><strong>List Property,</strong><span>and Delay the Launch.</span></div>
    <div class="tasks">
      <h3>In the meantime we will:</h3>
      <ul>
        <li>Prepare the contract<i></i></li>
        <li>Prepare marketing for the property<i></i></li>
        <li>Prepare the property for sale<i></i></li>
        <li>Do the Pest and Building Report<i></i></li>
        <li>Give the tenants their due notice of sale<i></i></li>
        <li>Advise buyers in an off market capacity<i></i></li>
      </ul>
    </div>
    <div class="rush">
      <h3>Beat the Rush.</h3>
      <p>This ensures we are first to market when the time comes, rather than arriving with a surge of spring sellers. Buyers are still buying now, and low stock is creating strength in the market.</p>
    </div>
    <div class="agent">
      <h4>firstname surname</h4>
      <p><i></i>0400 000 000</p>
      <p><i></i>agent@listlaunch.example</p>
    </div>
    <div class="perks">
      <div><svg width="12" height="12" viewBox="0 0 12 12"><rect x="2" y="1" width="8" height="10" fill="none" stroke="#2b2e3a"/></svg>Contract</div>
      <div><svg width="12" height="12" viewBox="0 0 12 12"><path d="M1 6 L6 1 L11 6 V11 H1 Z" fill="none" stroke="#2b2e3a"/></svg>Property</div>
      <div><svg width="12" height="12" viewBox="0 0 12 12"><circle cx="6" cy="6" r="5" fill="none" stroke="#2b2e3a"/></svg>Reports</div>
      <div><svg width="12" height="12" viewBox="0 0 12 12"><path d="M2 6 L5 9 L10 3" fill="none" stroke="#2b2e3a"/></svg>Buyers</div>
    </div>
  </section>

  <!-- Front, light -->
  <section class="flyer flyer--c front front--light">
    <div class="front__photo" role="img" aria-label="Bright living room interior photo, softly faded"></div>
    <div class="launch-mark" role="img" aria-label="Launch symbol: house taking off like a rocket"></div>
    <h1 class="front__headline">LIST NOW,<br>LAUNCH<br>LATER.</h1>
    <svg class="front__arrow" width="10" height="14" viewBox="0 0 10 14"><path d="M0 0 L10 7 L0 14 Z" fill="#f6a623"/></svg>
  </section>

  <!-- Back, dark -->
  <section class="flyer flyer--d back back--dark">
    <div class="back__mark" role="img" aria-label="Launch symbol: house taking off like a rocket"></div>
    <div class="back__title"><strong>List Property,</strong><span>and Delay the Launch.</span></div>
    <div class="tasks">
      <h3>In the meantime we will:</h3>
      <ul>
        <li>Prepare the contract<i></i></li>
        <li>Prepare marketing for the property<i></i></li>
        <li>Prepare the property for sale<i></i></li>
        <li>Do the Pest and Building Report<i></i></li>
        <li>Give the tenants their due notice of sale<i></i></li>
        <li>Advise buyers in an off market capacity<i></i></li>
      </ul>
    </div>
    <div class="rush">
      <h3>Beat the Rush.</h3>
      <p>This ensures we are first to market when the time comes, rather than arriving with a surge of spring sellers. Buyers are still buying now, and low stock is creating strength in the market.</p>
    </div>
    <div class="agent">
      <h4>firstname surname</h4>
      <p><i></i>0400 000 000</p>
      <p><i></i>agent@listlaunch.example</p>
    </div>
    <div class="perks">
      <div><svg width="12" height="12" viewBox="0 0 12 12"><rect x="2" y="1" width="8" height="10" fill="none" stroke="#fff"/></svg>Contract</div>
      <div><svg width="12" height="12" viewBox="0 0 12 12"><path d="M1 6 L6 1 L11 6 V11 H1 Z" fill="none" stroke="#fff"/></svg>Property</div>
      <div><svg width="12" height="12" viewBox="0 0 12 12"><circle cx="6" cy="6" r="5" fill="none" stroke="#fff"/></svg>Reports</div>
      <div><svg width="12" height="12" viewBox="0 0 12 12"><path d="M2 6 L5 9 L10 3" fill="none" stroke="#fff"/></svg>Buyers</div>
    </div>
  </section>

</body>
</html>
```